Modern Business Card

Modern professional business card with more than just logo and demographic info. Something memorable.

We are a trendy/modern chiropractic group with an emphasis on neurology, hence the minimalist-type brain logo. We want to convey that modern and technical aspect with professionalism and the elite nature of our practice environment.

```html
<!DOCTYPE html>
<html lang="en">
<head>
<meta charset="utf-8">
<title>Ardent Chiropractic – Business Card</title>
<link href="https://fonts.googleapis.com/css2?family=Roboto:wght@400&family=Lato:wght@400&display=swap" rel="stylesheet">
<style>
  :root {
    --page: #ffffff;
    --card: #262626;
    --band: #1d1d1d;
    --rule: #161616;
    --accent: #4a83c9;
    --ink: #f4f4f4;
    --glow: #323232;
  }
  * { margin: 0; padding: 0; box-sizing: border-box; }
  html, body { width: 1200px; height: 1200px; overflow: hidden; background: var(--page); }
  .canvas { position: relative; width: 1200px; height: 1200px; }

  .card { position: absolute; background: var(--card); overflow: hidden; }
  .card--front { left: 232px; top: 173px; width: 704px; height: 408px; }
  .card--back { left: 231px; top: 629px; width: 702px; height: 400px; }

  /* front */
  .brand-band { position: absolute; left: 0; top: 168px; width: 353px; height: 73px; background: var(--band); }
  .brand-dot { position: absolute; left: 54px; top: 168px; width: 72px; height: 72px; border-radius: 50%; background: var(--accent); }
  .brand-name { position: absolute; left: 148px; top: 178px; font-family: "Roboto", sans-serif; font-weight: 400; color: var(--ink); line-height: 1; }
  .brand-name__main { display: block; font-size: 38px; letter-spacing: 3px; }
  .brand-name__sub { display: block; font-size: 19px; letter-spacing: 1.5px; margin-top: 3px; }

  .divider { position: absolute; left: 352px; top: 85px; width: 2px; height: 240px; background: var(--rule); }

  .person { position: absolute; left: 382px; top: 86px; font-family: "Roboto", sans-serif; }
  .person__name { font-size: 34px; color: var(--accent); line-height: 1.1; }
  .person__role { font-size: 21px; color: var(--ink); margin-top: 2px; }

  .contacts { position: absolute; left: 353px; top: 174px; width: 293px; list-style: none; font-family: "Lato", sans-serif; font-size: 19px; color: var(--ink); }
  .contacts__row { position: relative; padding-left: 63px; height: 36px; line-height: 30px; border-bottom: 2px solid var(--rule); white-space: nowrap; }
  .contacts__row:last-child { border-bottom: none; height: auto; line-height: 24px; padding-top: 8px; }
  .contacts__icon { position: absolute; left: 29px; top: 7px; width: 20px; height: 18px; }
  .contacts__row:last-child .contacts__icon { top: 10px; }

  /* back */
  .back-texture { position: absolute; left: 0; top: 0; width: 380px; height: 400px;
    background: radial-gradient(ellipse 60% 55% at 50% 50%, var(--glow) 0%, rgba(38,38,38,0) 100%); }
  .back-dot { position: absolute; left: 106px; top: 134px; width: 126px; height: 126px; border-radius: 50%; background: var(--accent); }
  .back-name { position: absolute; left: 254px; top: 146px; font-family: "Roboto", sans-serif; font-weight: 400; color: var(--ink); line-height: 1; }
  .back-name__main { display: block; font-size: 74px; letter-spacing: 6px; }
  .back-name__sub { display: block; font-size: 44px; letter-spacing: 1.5px; margin-top: 6px; }
</style>
</head>
<body>
<main class="canvas">

  <section class="card card--front" aria-label="Card front">
    <div class="brand-band"></div>
    <div class="brand-dot"></div>
    <p class="brand-name"><span class="brand-name__main">ARDENT</span><span class="brand-name__sub">CHIROPRACTIC</span></p>

    <div class="divider"></div>

    <div class="person">
      <p class="person__name">Dorian Hale</p>
      <p class="person__role">President</p>
    </div>

    <ul class="contacts">
      <li class="contacts__row">
        <svg class="contacts__icon" viewBox="0 0 20 18" aria-hidden="true"><path fill="#4a83c9" d="M2 6c0-2 3-3 8-3s8 1 8 3v2h-4V6.5c-1-.6-7-.6-8 0V8H2zM5 9h10l2 6H3z"/><circle cx="10" cy="12" r="1.8" fill="#262626"/></svg>
        014 2758 3690
      </li>
      <li class="contacts__row">
        <svg class="contacts__icon" viewBox="0 0 20 18" aria-hidden="true"><path fill="#4a83c9" d="M1 2h15v10H1z"/><path fill="none" stroke="#262626" stroke-width="1.5" d="M1.5 2.5l7 5.5 7-5.5"/><circle cx="15" cy="13" r="4" fill="#4a83c9" stroke="#262626" stroke-width="1.2"/><path fill="none" stroke="#262626" stroke-width="1.3" d="M13 13l1.5 1.5 2.5-3"/></svg>
        hello@ardentchiro.com
      </li>
      <li class="contacts__row">
        <svg class="contacts__icon" viewBox="0 0 20 18" aria-hidden="true"><g fill="none" stroke="#4a83c9" stroke-width="1.4"><circle cx="10" cy="9" r="8"/><ellipse cx="10" cy="9" rx="3.5" ry="8"/><path d="M2 9h16M3.5 5h13M3.5 13h13"/></g></svg>
        www.ardentchiro.com
      </li>
      <li class="contacts__row">
        <svg class="contacts__icon" viewBox="0 0 20 18" aria-hidden="true"><path fill="#4a83c9" d="M10 0a6 6 0 0 1 6 6c0 4.5-6 12-6 12S4 10.5 4 6a6 6 0 0 1 6-6z"/><circle cx="10" cy="6" r="2.2" fill="#262626"/></svg>
        48 Linden Avenue 210<br>Portland, OR 97205
      </li>
    </ul>
  </section>

  <section class="card card--back" aria-label="Card back">
    <div class="back-texture" role="img" aria-label="Large faint brand pattern in the background"></div>
    <div class="back-dot"></div>
    <p class="back-name"><span class="back-name__main">ARDENT</span><span class="back-name__sub">CHIROPRACTIC</span></p>
  </section>

</main>
</body>
</html>
```